Business Card Design Project - del varosi group

dear Sirs

we need business card design for our group ( DEL Varosi Group ) , i have got the Logo design of our group from pixel harbor in previous , so all need details relating to our group i think available with you, as well as the the chosen logo design

we hope to provide us with business card logo that to be appropaite and satisfactory to us .

thanks

note : logo design of our group is attached .
Updates

Reason: please extend the deadline of my project for additional 15 days because i didn't received appropriate design for our gruop yet . kindly beaware that i have received 77 design till now , supossed to send me 200-250 design at least . thanks

Target Market(s)

contents

name : Kerem EL Nadiri

position : Operation Manager

Industry/Entity Type

Business

Requirements
Must have

• person name

group logo
Nice to have
• logo color matching with back background

```html
<!DOCTYPE html>
<html lang="en">
<head>
<meta charset="utf-8">
<title>DEL Varosi Group – Business Card</title>
<link rel="stylesheet" href="https://fonts.googleapis.com/css2?family=Open+Sans:wght@400;600;700&display=swap">
<style>
  :root {
    --brand-blue: #0f548f;
    --band-blue: #15558f;
    --card-white: #ffffff;
    --ink-grey: #4a4a4a;
    --page-bg: #e9e7e4;
  }
  * { box-sizing: border-box; margin: 0; padding: 0; }
  html, body { width: 1200px; height: 758px; overflow: hidden; }
  body {
    background: var(--page-bg);
    font-family: "Open Sans", sans-serif;
    position: relative;
  }
  .card {
    position: absolute;
    width: 520px;
    height: 300px;
    background: var(--card-white);
    border-radius: 26px;
    box-shadow: 0 6px 18px rgba(0,0,0,0.18);
  }
  .card--front { left: 60px; top: 229px; }
  .card--back  { left: 620px; top: 229px; }

  .name-band {
    position: absolute;
    left: 320px; top: 40px;
    width: 200px; height: 62px;
    background: var(--band-blue);
    color: #fff;
    padding: 10px 0 0 26px;
  }
  .name-band__name { font-weight: 700; font-size: 17px; line-height: 1.2; }
  .name-band__role { font-size: 12.5px; line-height: 1.4; }

  .contact-list {
    position: absolute;
    left: 330px; top: 118px;
    list-style: none;
    color: var(--ink-grey);
    font-size: 12.5px;
    line-height: 17px;
  }
  .contact-list li { display: flex; align-items: center; gap: 5px; }
  .contact-list svg { width: 9px; height: 9px; fill: var(--ink-grey); flex: none; }

  .address {
    position: absolute;
    left: 344px; top: 198px;
    color: var(--ink-grey);
    font-size: 12.5px;
    line-height: 18px;
  }

  .brand {
    position: absolute;
    display: flex;
    align-items: center;
    color: var(--brand-blue);
    font-weight: 700;
    white-space: nowrap;
  }
  .brand__mark { background: var(--brand-blue); flex: none; }
  .card--front .brand { left: 50px; top: 120px; font-size: 26px; gap: 10px; }
  .card--front .brand__mark { width: 16px; height: 16px; }
  .card--back .brand { left: 0; right: 0; top: 108px; justify-content: center; font-size: 38px; gap: 14px; }
  .card--back .brand__mark { width: 22px; height: 22px; }

  .website {
    position: absolute;
    color: var(--brand-blue);
    font-weight: 700;
  }
  .card--front .website { left: 120px; top: 238px; font-size: 12.5px; letter-spacing: 1.5px; }
  .card--back .website { left: 0; right: 0; top: 204px; text-align: center; font-size: 18px; font-weight: 600; letter-spacing: 1.5px; }
</style>
</head>
<body>
  <section class="card card--front" aria-label="Business card front">
    <div class="brand">
      <span class="brand__mark"></span>
      <span class="brand__name">DEL Varosi Group</span>
    </div>
    <p class="website">www.website.com</p>

    <div class="name-band">
      <p class="name-band__name">Kerem EL Nadiri</p>
      <p class="name-band__role">Operation Manager</p>
    </div>

    <ul class="contact-list">
      <li>
        <svg viewBox="0 0 10 10" aria-hidden="true"><rect x="2" y="0" width="6" height="10" rx="1"/></svg>
        +2348100457390
      </li>
      <li>
        <svg viewBox="0 0 10 10" aria-hidden="true"><path d="M2 0 L4 2.5 L3 4 Q4.5 6 6 7 L7.5 6 L10 8 L8.5 10 Q2 8 0 1.5 Z"/></svg>
        +2348100457390
      </li>
      <li>
        <svg viewBox="0 0 10 10" aria-hidden="true"><circle cx="5" cy="3" r="2.6"/><path d="M0.5 10 Q5 4 9.5 10 Z"/></svg>
        +2348100457390
      </li>
      <li>
        <svg viewBox="0 0 10 10" aria-hidden="true"><path d="M0 2 H10 V9 H0 Z M0 2 L5 6 L10 2" /></svg>
        name@harborlodge.com
      </li>
    </ul>

    <p class="address">Street name, City<br>State, zip code</p>
  </section>

  <section class="card card--back" aria-label="Business card back">
    <div class="brand">
      <span class="brand__mark"></span>
      <span class="brand__name">DEL Varosi Group</span>
    </div>
    <p class="website">www.website.com</p>
  </section>
</body>
</html>
```